Exciting new aperitif brand needs a great label

Vel-Orin is a wonderful rich new premium-priced bitter aperitif, with a deep red colour, from a 100+ year old distillery (1890) near Turin in the Piedmont region of Italy. Inspired by Tessoni, it is perfectly formulated to elevate the classic Bravetti cocktail (and variations on it). It also goes perfectly in a Spritz or a long mixed drink with soda or tonic. The name Vel-Orin is derived from the French for 'peak' and the Italian word for 'love'.

The label, which should take inspiration from Tessoni, but be distinctively different, can incoporate any number of premium label embellishments (foil, embossing, textures etc) and should be no greater than 11cm (height) x 9cm (width) with any core imagery restricted to a width of c.7cm.

The attached mood board should act as inspiration and colour should largely be restricted to reds, blues, whites and perhaps orange. For completeness, the label should note that the ABV is 25% and the bottle size 70cl.

Target Market(s)

21-45yr olds - equal split female/male

Colors
0054AA
0677BA
7BADD7
CADEEF
E8F1F8
0094D4
00A9DD
6FCCEA
C7EBF8
E9F6FB
EE7325
F08F49
F5BC92
FAE3D3
FDF4ED
EB3D1F
EC4F4E
F09395
F8D3D4
FCEDEE

Requirements
Must have
• Great lettering design on the name Vel-Orin

```html
<!DOCTYPE html>
<html lang="en">
<head>
<meta charset="utf-8">
<title>Vel-Orin Aperitif Label</title>
<link rel="stylesheet" href="https://fonts.googleapis.com/css2?family=Smokum&family=Alfa+Slab+One&display=swap">
<style>
  :root {
    --page: #ffffff;
    --navy: #0a1a5c;
    --navy-deep: #030a2e;
    --red: #a3181d;
    --red-deep: #6e0005;
    --gold: #d6962c;
    --gold-light: #f1cf6a;
    --silver: #e6e6e6;
    --silver-light: #ffffff;
    --silver-dark: #cfcfcf;
    --letter: #ffffff;
  }
  html, body {
    margin: 0;
    padding: 0;
    width: 1003px;
    height: 1200px;
    overflow: hidden;
    background: var(--page);
  }
  .label-canvas {
    display: block;
    width: 1003px;
    height: 1200px;
  }
  .brand-name {
    font-family: "Smokum", "Rye", serif;
    fill: var(--letter);
  }
  .abv-note {
    font-family: "Alfa Slab One", serif;
    fill: var(--gold);
    letter-spacing: 14px;
  }
</style>
</head>
<body>
<svg class="label-canvas" viewBox="0 0 1003 1200" xmlns="http://www.w3.org/2000/svg" role="img" aria-label="Vel-Orin aperitif label, 25% ABV">
  <defs>
    <linearGradient id="silver-band" x1="0" y1="0" x2="1" y2="0">
      <stop offset="0" stop-color="var(--silver-dark)"/>
      <stop offset="0.2" stop-color="var(--silver-light)"/>
      <stop offset="0.45" stop-color="var(--silver)"/>
      <stop offset="0.65" stop-color="var(--silver-light)"/>
      <stop offset="0.85" stop-color="var(--silver-dark)"/>
      <stop offset="1" stop-color="var(--silver-light)"/>
    </linearGradient>
    <linearGradient id="red-band" x1="0" y1="0" x2="1" y2="0">
      <stop offset="0" stop-color="var(--red-deep)"/>
      <stop offset="0.35" stop-color="var(--red)"/>
      <stop offset="0.75" stop-color="var(--red-deep)"/>
      <stop offset="1" stop-color="var(--red)"/>
    </linearGradient>
    <linearGradient id="navy-shield" x1="0" y1="0" x2="1" y2="0">
      <stop offset="0" stop-color="var(--navy)"/>
      <stop offset="0.5" stop-color="var(--navy-deep)"/>
      <stop offset="1" stop-color="var(--navy-deep)"/>
    </linearGradient>
    <linearGradient id="gold-frame" x1="0" y1="0" x2="1" y2="1">
      <stop offset="0" stop-color="var(--gold)"/>
      <stop offset="0.5" stop-color="var(--gold-light)"/>
      <stop offset="1" stop-color="var(--gold)"/>
    </linearGradient>
  </defs>

  <g class="label">
    <!-- panels -->
    <rect class="silver-panel" x="124" y="139" width="753" height="260" fill="url(#silver-band)"/>
    <rect class="red-panel" x="124" y="380" width="753" height="681" fill="url(#red-band)"/>

    <!-- silver chevron pinstripes -->
    <g class="silver-stripes" fill="none" stroke="var(--gold)" stroke-width="1">
      <polyline points="129,265 504,157 872,264"/>
      <polyline points="129,293 504,185 872,292"/>
      <polyline points="129,326 504,218 872,325"/>
    </g>

    <!-- red chevron pinstripes -->
    <g class="red-stripes" fill="none" stroke="#d66a6a" stroke-opacity="0.35" stroke-width="1">
      <polyline points="129,860 504,968 872,860"/>
      <polyline points="129,888 504,996 872,888"/>
      <polyline points="129,930 504,1038 872,930"/>
    </g>

    <!-- gold frame -->
    <rect class="gold-frame" x="129.5" y="144.5" width="742" height="911" fill="none" stroke="url(#gold-frame)" stroke-width="11"/>

    <!-- navy shield -->
    <polygon class="navy-shield" points="51,395 504,258 949,400 949,809 504,946 51,809" fill="url(#navy-shield)"/>
    <g class="shield-lines" fill="none" stroke="var(--gold)" stroke-width="2">
      <polyline points="140,389 504,283 868,389" stroke-opacity="0.9"/>
      <polyline points="110,815 504,928 905,812" stroke="var(--gold-light)" stroke-opacity="0.9"/>
    </g>

    <!-- name -->
    <text class="brand-name" x="504" y="738" text-anchor="middle" font-size="330" textLength="840" lengthAdjust="spacingAndGlyphs">VEL-ORIN</text>

    <!-- ABV -->
    <text class="abv-note" x="511" y="1000" text-anchor="middle" font-size="30">25% ABV</text>
  </g>
</svg>
</body>
</html>
```